Orvane Mechanical - Letterhead

We are a plumbing and hvac company based in Calgary. This letterhead will be on our quotes, invoices, preventative maintenance proposals etc.

```html
<!DOCTYPE html>
<html lang="en">
<head>
<meta charset="utf-8">
<title>Orvane Mechanical – Letterhead</title>
<link rel="stylesheet" href="https://fonts.googleapis.com/css2?family=Lato:wght@300;400;700;900&display=swap">
<style>
  :root {
    --brand-orange: #f15a29;
    --brand-blue: #1b73ba;
    --ink: #4a4a4a;
    --paper: #ffffff;
    --backdrop: #e9e9e9;
  }
  * { margin: 0; padding: 0; box-sizing: border-box; }
  html, body {
    width: 1056px; height: 1200px; overflow: hidden;
    background: var(--backdrop);
    font-family: "Lato", Arial, sans-serif;
  }
  .letterhead {
    position: absolute; left: 104px; top: 0;
    width: 1065px; height: 1507px;
    background: var(--paper);
    transform: scale(0.7963); transform-origin: top left;
  }
  .side-band { position: absolute; left: 0; top: 0; width: 52px; height: 1507px; }
  .company-mark {
    position: absolute; left: 115px; top: 150px;
    display: flex; align-items: center; gap: 14px;
  }
  .company-mark .dot {
    width: 22px; height: 22px; border-radius: 50%; background: var(--brand-orange);
  }
  .company-name {
    font-weight: 900; font-size: 38px; color: var(--brand-blue);
    letter-spacing: 0.5px;
  }
  .contact-bar {
    position: absolute; left: 28px; top: 1273px;
    width: 42px; height: 193px;
    background: var(--brand-orange);
    border: 5px solid var(--paper);
    outline: 0;
  }
  .contact-icon { position: absolute; left: 5px; width: 22px; height: 22px; }
  .contact-list {
    position: absolute; left: 81px; top: 1290px;
    list-style: none; color: var(--ink);
    font-weight: 300; font-size: 22px; line-height: 26px;
  }
  .contact-list .gap { height: 26px; }
  .contact-list .accent { color: var(--brand-orange); }
</style>
</head>
<body>
<div class="letterhead">
  <svg class="side-band" viewBox="0 0 52 1507" preserveAspectRatio="none" aria-hidden="true">
    <polygon points="0,0 52,0 52,400 0,370" fill="var(--brand-orange)"/>
    <polygon points="0,385 52,415 52,1507 0,1507" fill="var(--brand-blue)"/>
  </svg>

  <div class="company-mark">
    <span class="dot"></span>
    <span class="company-name">Orvane Mechanical</span>
  </div>

  <div class="contact-bar">
    <svg class="contact-icon" style="top:23px" viewBox="0 0 24 24" aria-hidden="true">
      <path d="M12 2a7 7 0 0 0-7 7c0 5 7 13 7 13s7-8 7-13a7 7 0 0 0-7-7z" fill="#fff"/>
      <circle cx="12" cy="9" r="2.6" fill="var(--brand-orange)"/>
    </svg>
    <svg class="contact-icon" style="top:95px" viewBox="0 0 24 24" aria-hidden="true">
      <path d="M6.6 10.8a15 15 0 0 0 6.6 6.6l2.2-2.2c.3-.3.7-.4 1-.2 1.1.4 2.3.6 3.6.6.6 0 1 .4 1 1V20c0 .6-.4 1-1 1A17 17 0 0 1 3 4c0-.6.4-1 1-1h3.5c.6 0 1 .4 1 1 0 1.3.2 2.5.6 3.6.1.3 0 .7-.2 1z" fill="#fff"/>
    </svg>
    <svg class="contact-icon" style="top:124px" viewBox="0 0 24 24" aria-hidden="true">
      <rect x="3" y="6" width="18" height="12" fill="none" stroke="#fff" stroke-width="1.8"/>
      <path d="M3 6l9 7 9-7" fill="none" stroke="#fff" stroke-width="1.8"/>
    </svg>
    <svg class="contact-icon" style="top:153px" viewBox="0 0 24 24" aria-hidden="true">
      <circle cx="12" cy="12" r="8.5" fill="none" stroke="#fff" stroke-width="1.6"/>
      <ellipse cx="12" cy="12" rx="3.8" ry="8.5" fill="none" stroke="#fff" stroke-width="1.3"/>
      <path d="M3.5 12h17M5 8h14M5 16h14" stroke="#fff" stroke-width="1.3"/>
    </svg>
  </div>

  <ul class="contact-list">
    <li>1234 First Line Address</li>
    <li>5678 Second Line Address</li>
    <li class="gap"></li>
    <li style="margin-top:0">(111) 999-0000</li>
    <li style="margin-top:3px">Info@yourmail.com</li>
    <li style="margin-top:4px">www.<span class="accent">yourwebsite</span>.com</li>
  </ul>
</div>
</body>
</html>
```